Corvane Grid Works Ltd. -Website Design

We need a site design for a new company based in Toronto, Ontario called 'Corvane Grid Works Ltd.'

We provide Engineering services, Subsurface Utility Engineering services and Geospatial Data Management.

Our clients are typically Utilities (electric, gas, water/waste water, telcom) or contractors/consultants working on their behalf.

Our business model is new and we are the first to offer all three services to our clients; this allows us to provide value-added services from all three of our main offerings.

Target Market(s)

Field Supervisors, Managers, Directors, VP's at Utility companies

Industry/Entity Type

Business

Requirements
Must have
• -The landing page must clearly identify the 3 main business offerings allowing the user to easily navigate to each....Utility Engineering, GIS Data Management & Sub-surface Utility Engineering (SUE).

-Interactive contact page with integrated email

-based on existing logo design...
Nice to have
• -Ability to easily add/post news releases, updates, jobs, etc...

-Ability to integrate instructional YouTube video(s)

Should not have
• -Cannot be too cluttered....

```html
<!DOCTYPE html>
<html lang="en">
<head>
<meta charset="utf-8">
<title>Corvane Grid Works Ltd. — Utility Services</title>
<link href="https://fonts.googleapis.com/css2?family=Open+Sans:wght@400;600;700&family=Ubuntu:wght@400;500;700&display=swap" rel="stylesheet">
<style>
:root{
  --dark:#333335;
  --header:#404042;
  --light-band:#ececec;
  --white:#ffffff;
  --teal:#1c7393;
  --yellow:#f3e63a;
  --orange:#f39a2e;
  --text-light:#d8d8d8;
  --footer:#454547;
  --wing:#c9c9c9;
}
*{margin:0;padding:0;box-sizing:border-box}
html,body{width:1006px;height:1200px;overflow:hidden}
body{position:relative;background:var(--dark);font-family:Arial,Helvetica,sans-serif;color:var(--white)}
.band{position:absolute;left:0;width:1006px}
.band-top{top:0;height:218px;background:var(--dark)}
.band-light{top:218px;height:266px;background:var(--light-band)}
.band-white{top:484px;height:136px;background:var(--white)}
.band-main{top:620px;height:460px;background:var(--dark)}
.band-footer{top:1080px;height:120px;background:var(--footer);border-top:3px solid #2c2c2e}

.site-header{position:absolute;left:109px;top:0;width:787px;height:129px;background:var(--header);border:1px solid #4e4e50}
.brand{position:absolute;left:18px;top:44px;display:flex;align-items:center;gap:12px}
.brand-mark{width:40px;height:40px;border:4px solid var(--orange);border-radius:6px}
.brand-name{font-family:'Ubuntu',sans-serif;font-weight:700;font-size:22px;letter-spacing:2px;color:var(--white)}
.nav{position:absolute;right:30px;top:47px;display:flex;align-items:center;font-family:'Ubuntu',sans-serif;font-size:16px;font-weight:500}
.nav a{color:var(--white);text-decoration:none;padding:0 20px;line-height:40px}
.nav .active{background:linear-gradient(#2f9cc4,#1a7599);border:1px solid #5bbde0;border-radius:3px;margin-right:12px}
.nav .divider{width:1px;height:30px;background:#777}

.wing{position:absolute;top:142px}
.wing-left{left:89px}
.wing-right{left:896px}

.slider{position:absolute;left:109px;top:142px;width:788px;height:396px;background:var(--white);padding:6px;box-shadow:0 6px 10px rgba(0,0,0,.25)}
.slider-photo{width:100%;height:100%;background:linear-gradient(160deg,#8a7d6a 0%,#c9c3b8 30%,#e9e7e4 55%,#bdb7b0 80%,#7d3a2e 100%)}
.slider-dots{position:absolute;left:334px;bottom:10px;width:128px;height:42px;background:rgba(40,40,40,.8);border-radius:8px 8px 0 0;display:flex;justify-content:center;align-items:center;gap:8px}
.slider-dots span{width:14px;height:14px;border-radius:50%;background:#bdb58a}
.slider-dots span.on{background:var(--yellow)}

.service{position:absolute;top:559px;width:252px;height:279px;background:var(--teal);border-radius:8px;padding:16px 22px}
.service h2{font-family:'Ubuntu',sans-serif;font-weight:500;font-size:22px;line-height:26px;letter-spacing:.5px;margin-bottom:16px;text-transform:uppercase;min-height:52px}
.service.sm h2{font-size:19px}
.service ul{list-style:none}
.service li{font-size:11.2px;line-height:13px;margin-bottom:9px;padding-left:21px;position:relative;color:#eef6fa}
.service li svg{position:absolute;left:0;top:1px}
.btn-more{position:absolute;left:23px;bottom:17px;width:85px;height:31px;background:linear-gradient(#4a4a4a,#1a1a1a);border:1px solid #0e0e0e;color:var(--white);font-family:'Ubuntu',sans-serif;font-size:16px;line-height:29px;text-align:center}

.col{position:absolute;top:860px}
.col h3{font-family:'Ubuntu',sans-serif;font-weight:400;font-size:21px;margin-bottom:12px;letter-spacing:.5px}
.welcome{left:109px;width:250px}
.welcome p{font-size:11px;line-height:19.4px;color:var(--text-light)}
.btn-blue{display:block;margin-top:14px;width:84px;height:30px;background:linear-gradient(#2f9cc4,#1a7599);border:1px solid #5bbde0;color:var(--white);font-family:'Ubuntu',sans-serif;font-size:16px;line-height:28px;text-align:center}
.contact{left:390px;width:220px}
.field{width:220px;height:24px;margin-bottom:7px;background:linear-gradient(#fafafa,#dcdcdc);border:1px solid #aaa;border-radius:3px;color:#666;font-size:11px;padding:5px 12px}
.field.area{height:66px}
.btn-submit{float:right;margin-top:7px;width:68px;height:23px;background:linear-gradient(#2f9cc4,#1a7599);border:1px solid #5bbde0;font-family:'Ubuntu',sans-serif;font-size:13px;line-height:21px;text-align:center}
.video{left:645px;width:256px}
.video-frame{width:256px;height:163px;border:3px solid #bfbfbf;background:linear-gradient(160deg,#2a2a2a,#111);position:relative}
.video-frame .play{position:absolute;left:98px;top:42px;width:56px;height:56px;border-radius:50%;background:rgba(120,120,120,.85)}
.video-frame .play svg{position:absolute;left:20px;top:16px}
.video-frame .label{position:absolute;left:0;right:0;top:72px;text-align:center;font-family:'Open Sans',sans-serif;font-size:12px}

.footer-brand{position:absolute;left:109px;top:1097px;display:flex;align-items:center;gap:8px}
.footer-brand .brand-mark{width:32px;height:32px;border:3px solid #8a8a8a}
.footer-brand .brand-name{font-size:18px;color:#cfcfcf}
.copyright{position:absolute;left:109px;top:1143px;font-size:10.5px;color:#ddd}
.footer-col{position:absolute;top:1105px;font-size:10px;line-height:17px;color:#ddd}
.footer-col h4{font-weight:400;font-size:13px;color:var(--white);margin-bottom:2px}
.address{left:444px}
.follow{left:732px}
.follow ul{list-style:none}
.follow li{display:flex;align-items:center;gap:7px;margin-bottom:3px}
.follow .ico{width:16px;height:16px;background:#3b5998;border-radius:2px}
.follow .ico.b{background:#4ab3e6}
.follow .ico.c{background:#cfd9e6}
.follow .mail{color:var(--orange)}
</style>
</head>
<body>
<div class="band band-top"></div>
<div class="band band-light"></div>
<div class="band band-white"></div>
<div class="band band-main"></div>
<div class="band band-footer"></div>

<header class="site-header">
  <div class="brand"><span class="brand-mark"></span><span class="brand-name">CORVANE GRID WORKS</span></div>
  <nav class="nav">
    <a class="active" href="#">HOME</a>
    <a href="#">SERVICES</a>
    <span class="divider"></span>
    <a href="#">CONTACT US</a>
  </nav>
</header>

<svg class="wing wing-left" width="20" height="78"><path d="M20 0V78H0Z" fill="#c9c9c9"/></svg>
<svg class="wing wing-right" width="20" height="78"><path d="M0 0V78H20Z" fill="#c9c9c9"/></svg>

<section class="slider">
  <div class="slider-photo" role="img" aria-label="Engineer in a white hard hat holding rolled plans outside a building"></div>
  <div class="slider-dots"><span class="on"></span><span></span><span></span><span></span></div>
</section>

<section class="service" style="left:109px">
  <h2>Utility<br>Engineering</h2>
  <ul>
    <li><svg width="11" height="11"><path d="M8 1v6H2M4 5L2 7l2 2" stroke="#f3e63a" stroke-width="2" fill="none"/></svg>Project Management.</li>
    <li><svg width="11" height="11"><path d="M8 1v6H2M4 5L2 7l2 2" stroke="#f3e63a" stroke-width="2" fill="none"/></svg>Outside Plant Network Design.</li>
    <li><svg width="11" height="11"><path d="M8 1v6H2M4 5L2 7l2 2" stroke="#f3e63a" stroke-width="2" fill="none"/></svg>Utility Design and Permitting.</li>
    <li><svg width="11" height="11"><path d="M8 1v6H2M4 5L2 7l2 2" stroke="#f3e63a" stroke-width="2" fill="none"/></svg>Project Management.</li>
    <li><svg width="11" height="11"><path d="M8 1v6H2M4 5L2 7l2 2" stroke="#f3e63a" stroke-width="2" fill="none"/></svg>Surveys and Mapping (GPS).</li>
    <li><svg width="11" height="11"><path d="M8 1v6H2M4 5L2 7l2 2" stroke="#f3e63a" stroke-width="2" fill="none"/></svg>Pole line design and attachment permitting (Pole Load Calculations).</li>
  </ul>
  <a class="btn-more">MORE</a>
</section>

<section class="service" style="left:377px">
  <h2>GIS Data<br>Management</h2>
  <ul>
    <li><svg width="11" height="11"><path d="M8 1v6H2M4 5L2 7l2 2" stroke="#f3e63a" stroke-width="2" fill="none"/></svg>GIS Project Management.</li>
    <li><svg width="11" height="11"><path d="M8 1v6H2M4 5L2 7l2 2" stroke="#f3e63a" stroke-width="2" fill="none"/></svg>Records Conversion for GIS Systems.</li>
    <li><svg width="11" height="11"><path d="M8 1v6H2M4 5L2 7l2 2" stroke="#f3e63a" stroke-width="2" fill="none"/></svg>Landbase Data Management.</li>
    <li><svg width="11" height="11"><path d="M8 1v6H2M4 5L2 7l2 2" stroke="#f3e63a" stroke-width="2" fill="none"/></svg>Hydro Asset Management using Tarnwick Atlas.</li>
    <li><svg width="11" height="11"><path d="M8 1v6H2M4 5L2 7l2 2" stroke="#f3e63a" stroke-width="2" fill="none"/></svg>Spatial Data Analysis &amp; Manipulation.</li>
  </ul>
  <a class="btn-more">MORE</a>
</section>

<section class="service sm" style="left:645px">
  <h2>Sub-Surface Utility<br>Engineering (SUE)</h2>
  <ul>
    <li><svg width="11" height="11"><path d="M8 1v6H2M4 5L2 7l2 2" stroke="#f3e63a" stroke-width="2" fill="none"/></svg>Project Management.</li>
    <li><svg width="11" height="11"><path d="M8 1v6H2M4 5L2 7l2 2" stroke="#f3e63a" stroke-width="2" fill="none"/></svg>Consulting.</li>
    <li><svg width="11" height="11"><path d="M8 1v6H2M4 5L2 7l2 2" stroke="#f3e63a" stroke-width="2" fill="none"/></svg>Surveying.</li>
    <li><svg width="11" height="11"><path d="M8 1v6H2M4 5L2 7l2 2" stroke="#f3e63a" stroke-width="2" fill="none"/></svg>CAD Processing of Results.</li>
  </ul>
  <a class="btn-more">MORE</a>
</section>

<section class="col welcome">
  <h3>Welcome to Our Site!</h3>
  <p>Lorem ipsum dolor sit amet, consectetur adipiscing elit. Fusce accumsan, elit a suscipit sagittis, tortor sapien cursus risus, non rhoncus lectus nunc ac nulla. Aliquam molestie, mi et imperdiet euismod, dui purus auctor tellus, et interdum lacus lectus et ante.</p>
  <a class="btn-blue">MORE</a>
</section>

<section class="col contact">
  <h3>Quick Contact</h3>
  <div class="field">Name</div>
  <div class="field">Email Address</div>
  <div class="field area">Email Address</div>
  <div class="btn-submit">Submit</div>
</section>

<section class="col video">
  <h3>Watch a Video</h3>
  <div class="video-frame">
    <div class="play"><svg width="20" height="24"><path d="M0 0L20 12L0 24Z" fill="#111"/></svg></div>
    <div class="label">Click for a play</div>
  </div>
</section>

<footer>
  <div class="footer-brand"><span class="brand-mark"></span><span class="brand-name">CORVANE GRID WORKS</span></div>
  <div class="copyright">© 2012 corvanegrid.ca. All Rights Reserved</div>
  <div class="footer-col address">
    <h4>Contact Address:</h4>
    418-2 Halden Crt, Toronto,<br>ON M4B 2K7 T - 416.555.0148<br>F - 416.555.0162
  </div>
  <div class="footer-col follow">
    <h4>Follow us on:</h4>
    <ul>
      <li><span class="ico"></span>Friendwall</li>
      <li><span class="ico b"></span>Chirpline</li>
      <li><span class="ico c"></span>Email : <span class="mail">info@corvanegrid.ca</span></li>
    </ul>
  </div>
</footer>
</body>
</html>
```